PowerPoint Corporate Template for Healthcare AI Technology Company

Take logo and create a comprehensive source file for corporate PowerPoint presentation library that provides an array of title/separator slides, graphic presentation options, chart options and text slide options. Utilize the current logo files and provide options on white backgrounds, and knock out options.

Target Market(s)

Pharmaceutical Manufacturers

Font styles to use
Sans Serif

Colors
6b449b
0556a4
33a6d7
0393ce
ffffff
e34197

Requirements
Must have
• Use logos upgraded in files; create an embedded color palette that aligns to the logo; include multiple options for different types of slides including charts; create a bullet point that is the logo in the purple/blue color with white background; incorporate knock out logo version option for separator pages; must include page numbers; use font aligned to logo for text slide options
Nice to have
• Tech looking, data intensive slide options that communicate easily; could be using 3-4 data points per slide
Should not have
• Any logo other than what has been shared

```html
<!DOCTYPE html>
<html lang="en">
<head>
<meta charset="utf-8">
<title>Veltrano Corporate Slide Library</title>
<link rel="stylesheet" href="https://fonts.googleapis.com/css2?family=Roboto:wght@300;400;500;700;900&display=swap">
<style>
  :root {
    --purple: #6b449b;
    --navy: #0556a4;
    --sky: #33a6d7;
    --azure: #0393ce;
    --line-blue: #1a9ad6;
    --white: #ffffff;
    --ink: #05050d;
    --text-grey: #333740;
    --footer-grey: #8b9097;
    --lilac: #ddd1ea;
    --page: #e9e9ea;
  }
  html, body {
    margin: 0;
    padding: 0;
    overflow: hidden;
  }
  body {
    width: 1037px;
    height: 1200px;
    background: var(--page);
    font-family: "Roboto", Arial, sans-serif;
    position: relative;
  }
  .slide {
    position: absolute;
    display: block;
    box-shadow: 0 2px 6px rgba(0, 0, 0, 0.18);
  }
  .title-slide { left: 210px; top: 162px; width: 610px; height: 343px; }
  .flow-slide { left: 42px; top: 631px; width: 453px; height: 255px; }
  .hub-slide { left: 538px; top: 631px; width: 453px; height: 255px; }
  .ring-slide { left: 42px; top: 911px; width: 453px; height: 255px; }
  .data-slide { left: 538px; top: 911px; width: 453px; height: 255px; }
  .symbols { position: absolute; width: 0; height: 0; }

  .slide text { font-family: "Roboto", Arial, sans-serif; }
  .heading { font-weight: 700; fill: var(--white); }
  .brand { font-weight: 300; fill: var(--purple); }
  .item-title { font-weight: 500; font-size: 11px; fill: var(--ink); }
  .item-body { font-weight: 400; font-size: 8.6px; fill: var(--text-grey); }
  .hub-title { font-weight: 500; font-size: 11px; fill: var(--white); }
  .hub-body { font-weight: 400; font-size: 8.6px; fill: #d8ecf3; }
  .node-text { font-weight: 400; font-size: 7.4px; fill: var(--white); }
  .footer-url { font-weight: 400; font-size: 10px; fill: var(--white); letter-spacing: 0.6px; }
  .band-text { font-weight: 400; font-size: 10.5px; fill: var(--white); }
  .arc-text { font-weight: 400; font-size: 10px; fill: var(--white); }
  .chart-label { font-weight: 400; font-size: 8px; fill: var(--white); }
  .group-label { font-weight: 400; font-size: 10.5px; fill: var(--sky); letter-spacing: 0.4px; }
  .pct { font-weight: 700; font-size: 8px; fill: var(--white); }
</style>
</head>
<body>

<svg class="symbols" aria-hidden="true">
  <defs>
    <symbol id="icon-docs" viewBox="0 0 24 24">
      <g fill="none" stroke="currentColor" stroke-width="1.4">
        <rect x="3" y="2" width="13" height="17"/>
        <line x1="6" y1="6" x2="13" y2="6"/>
        <line x1="6" y1="9" x2="13" y2="9"/>
        <line x1="6" y1="12" x2="10" y2="12"/>
        <circle cx="16" cy="14" r="3"/>
        <path d="M11 22c0-3 2.2-4.5 5-4.5s5 1.5 5 4.5z"/>
      </g>
    </symbol>
    <symbol id="icon-person" viewBox="0 0 12 30">
      <circle cx="6" cy="3" r="2.8" fill="currentColor"/>
      <rect x="2" y="7" width="8" height="11" rx="1.5" fill="currentColor"/>
      <rect x="0" y="7.5" width="1.6" height="9" rx="0.8" fill="currentColor"/>
      <rect x="10.4" y="7.5" width="1.6" height="9" rx="0.8" fill="currentColor"/>
      <rect x="2.6" y="17" width="2.8" height="12" rx="1" fill="currentColor"/>
      <rect x="6.6" y="17" width="2.8" height="12" rx="1" fill="currentColor"/>
    </symbol>
    <marker id="arrow-blue" viewBox="0 0 10 10" refX="8" refY="5" markerWidth="5" markerHeight="5" orient="auto">
      <path d="M0 0 L10 5 L0 10 z" fill="#1a9ad6"/>
    </marker>
  </defs>
</svg>

<!-- Title / separator slide -->
<svg class="slide title-slide" viewBox="0 0 1054 593" xmlns="http://www.w3.org/2000/svg">
  <defs>
    <radialGradient id="title-glow" cx="0.5" cy="0.72" r="0.75">
      <stop offset="0" stop-color="#3fa0ff"/>
      <stop offset="0.35" stop-color="#0b4fc4"/>
      <stop offset="0.7" stop-color="#062a86"/>
      <stop offset="1" stop-color="#03124a"/>
    </radialGradient>
    <linearGradient id="horizon" x1="0" x2="1">
      <stop offset="0" stop-color="#2f8bff" stop-opacity="0.2"/>
      <stop offset="0.5" stop-color="#bfe6ff"/>
      <stop offset="1" stop-color="#2f8bff" stop-opacity="0.2"/>
    </linearGradient>
  </defs>
  <rect width="1054" height="593" fill="url(#title-glow)" role="img" aria-label="Blue technology backdrop with glowing concentric circuit rings"/>
  <rect x="0" y="428" width="1054" height="10" fill="url(#horizon)"/>
  <rect x="0" y="438" width="1054" height="155" fill="#041f7a" opacity="0.55"/>
  <path d="M302 425 A224 224 0 0 1 750 425 Z" fill="var(--white)"/>
  <text class="brand" x="526" y="365" font-size="74" text-anchor="middle">Veltrano</text>
  <text class="heading" x="526" y="525" font-size="62" text-anchor="middle" font-weight="900">HEADING GOES HERE</text>
  <text x="526" y="570" font-size="21" fill="#ffffff" text-anchor="middle" letter-spacing="6">www.webaddress.com</text>
</svg>

<!-- Process flow slide -->
<svg class="slide flow-slide" viewBox="0 0 782 440" xmlns="http://www.w3.org/2000/svg">
  <rect width="782" height="440" fill="var(--white)"/>
  <rect width="782" height="60" fill="var(--ink)"/>
  <circle cx="49" cy="30" r="18" fill="none" stroke="var(--sky)" stroke-width="2"/>
  <text class="heading" x="78" y="38" font-size="21">HEADING GOES HERE</text>

  <g fill="none" stroke="var(--line-blue)" stroke-width="2">
    <path d="M505 174 H505 V110 H402" marker-end="url(#arrow-blue)"/>
    <path d="M505 174 H482" marker-end="url(#arrow-blue)"/>
    <path d="M410 174 H278 V238 H306" marker-end="url(#arrow-blue)"/>
    <path d="M372 238 H502 V300 H478" marker-end="url(#arrow-blue)"/>
    <path d="M412 300 H278 V364 H324" marker-end="url(#arrow-blue)"/>
  </g>
  <g fill="var(--white)" stroke="var(--line-blue)" stroke-width="2.5">
    <circle cx="345" cy="110" r="28"/>
    <circle cx="440" cy="174" r="28"/>
    <circle cx="342" cy="238" r="28"/>
    <circle cx="442" cy="300" r="28"/>
    <circle cx="360" cy="364" r="28"/>
  </g>
  <g color="#222">
    <use href="#icon-docs" x="329" y="94" width="32" height="32"/>
    <use href="#icon-docs" x="424" y="158" width="32" height="32"/>
    <use href="#icon-docs" x="326" y="222" width="32" height="32"/>
    <use href="#icon-docs" x="426" y="284" width="32" height="32"/>
    <use href="#icon-docs" x="344" y="348" width="32" height="32"/>
  </g>

  <g>
    <text class="item-title" x="521" y="125">Sample Text Here</text>
    <text class="item-body" x="521" y="141">Lorem Ipsum is simply dummy text of the printing</text>
    <text class="item-body" x="521" y="154">and typesetting industry. Lorem Ipsum has been the</text>
    <text class="item-body" x="521" y="167">industry's standard dummy text</text>

    <text class="item-title" x="521" y="250">Sample Text Here</text>
    <text class="item-body" x="521" y="266">Lorem Ipsum is simply dummy text of the printing</text>
    <text class="item-body" x="521" y="279">and typesetting industry. Lorem Ipsum has been the</text>
    <text class="item-body" x="521" y="292">industry's standard dummy text</text>
  </g>
  <g text-anchor="end">
    <text class="item-title" x="260" y="187">Sample Text Here</text>
    <text class="item-body" x="260" y="203">Lorem Ipsum is simply dummy text of the printing</text>
    <text class="item-body" x="260" y="216">and typesetting industry. Lorem Ipsum has been the</text>
    <text class="item-body" x="260" y="229">industry's standard dummy text</text>

    <text class="item-title" x="260" y="313">Sample Text Here</text>
    <text class="item-body" x="260" y="329">Lorem Ipsum is simply dummy text of the printing</text>
    <text class="item-body" x="260" y="342">and typesetting industry. Lorem Ipsum has been the</text>
    <text class="item-body" x="260" y="355">industry's standard dummy text</text>
  </g>

  <rect x="0" y="405" width="180" height="22" fill="var(--footer-grey)"/>
  <circle cx="20" cy="416" r="5" fill="none" stroke="var(--white)" stroke-width="1.2"/>
  <text class="footer-url" x="34" y="420">www.webaddress.com | 2</text>
  <line x1="194" y1="416" x2="650" y2="416" stroke="#9aa0a6" stroke-width="1"/>
  <circle cx="191" cy="416" r="3" fill="var(--white)" stroke="#9aa0a6"/>
  <text class="brand" x="765" y="423" font-size="22" text-anchor="end">Veltrano</text>
</svg>

<!-- Hub diagram slide -->
<svg class="slide hub-slide" viewBox="0 0 782 440" xmlns="http://www.w3.org/2000/svg">
  <defs>
    <linearGradient id="teal-bg" x1="0" y1="0" x2="0.4" y2="1">
      <stop offset="0" stop-color="#123f74"/>
      <stop offset="0.55" stop-color="#14577f"/>
      <stop offset="1" stop-color="#1a9a8c"/>
    </linearGradient>
  </defs>
  <rect width="782" height="440" fill="url(#teal-bg)"/>

  <g stroke-width="4">
    <line x1="380" y1="199" x2="303" y2="110" stroke="#6cc24a"/>
    <line x1="303" y1="110" x2="303" y2="44" stroke="#6cc24a"/>
    <line x1="380" y1="199" x2="380" y2="98" stroke="#2cb87a"/>
    <line x1="380" y1="199" x2="476" y2="125" stroke="#33b36a"/>
    <line x1="476" y1="125" x2="530" y2="88" stroke="#33b36a"/>
    <line x1="380" y1="199" x2="535" y2="180" stroke="#1fb89a"/>
    <line x1="535" y1="180" x2="595" y2="176" stroke="#1fb89a"/>
    <line x1="380" y1="199" x2="190" y2="199" stroke="#2cb87a"/>
    <line x1="380" y1="199" x2="308" y2="265" stroke="#0d8ed0"/>
    <line x1="308" y1="265" x2="257" y2="303" stroke="#0d8ed0"/>
    <line x1="380" y1="199" x2="380" y2="378" stroke="#1fb89a"/>
    <line x1="380" y1="199" x2="490" y2="267" stroke="#1ec8d0"/>
    <line x1="490" y1="267" x2="578" y2="326" stroke="#1ec8d0"/>
  </g>

  <g>
    <circle cx="303" cy="110" r="38" fill="#6cc24a"/>
    <circle cx="476" cy="125" r="38" fill="#33b36a"/>
    <circle cx="535" cy="180" r="32" fill="var(--white)"/>
    <circle cx="261" cy="199" r="37" fill="#2cb87a"/>
    <circle cx="308" cy="265" r="32" fill="#0d8ed0"/>
    <circle cx="380" cy="305" r="37" fill="#1fb89a"/>
    <circle cx="490" cy="267" r="57" fill="#1ec8d0"/>
    <circle cx="380" cy="199" r="58" fill="#2ec27e"/>
    <circle cx="380" cy="199" r="51" fill="var(--white)"/>
  </g>
  <text class="brand" x="380" y="204" font-size="18" text-anchor="middle">Veltrano</text>

  <g fill="var(--white)" stroke-width="2">
    <circle cx="303" cy="44" r="10" stroke="#6cc24a"/>
    <circle cx="380" cy="98" r="13" stroke="#2cb87a"/>
    <circle cx="530" cy="88" r="10" stroke="#33b36a"/>
    <circle cx="595" cy="176" r="9" stroke="#1fb89a"/>
    <circle cx="190" cy="199" r="9" stroke="#2cb87a"/>
    <circle cx="257" cy="303" r="8" stroke="#0d8ed0"/>
    <circle cx="380" cy="378" r="9" stroke="#1fb89a"/>
    <circle cx="578" cy="326" r="13" stroke="#1ec8d0"/>
  </g>
  <g color="#2d5a6a">
    <use href="#icon-docs" x="297" y="38" width="12" height="12"/>
    <use href="#icon-docs" x="372" y="90" width="16" height="16"/>
    <use href="#icon-docs" x="524" y="82" width="12" height="12"/>
    <use href="#icon-docs" x="589" y="170" width="12" height="12"/>
    <use href="#icon-docs" x="184" y="193" width="12" height="12"/>
    <use href="#icon-docs" x="252" y="298" width="10" height="10"/>
    <use href="#icon-docs" x="374" y="372" width="12" height="12"/>
    <use href="#icon-docs" x="570" y="318" width="16" height="16"/>
    <use href="#icon-docs" x="526" y="162" width="18" height="18"/>
  </g>
  <g color="#ffffff">
    <use href="#icon-docs" x="294" y="86" width="18" height="18"/>
    <use href="#icon-docs" x="467" y="101" width="18" height="18"/>
    <use href="#icon-docs" x="252" y="175" width="18" height="18"/>
    <use href="#icon-docs" x="299" y="243" width="18" height="18"/>
    <use href="#icon-docs" x="371" y="281" width="18" height="18"/>
    <use href="#icon-docs" x="481" y="236" width="18" height="18"/>
  </g>
  <g text-anchor="middle">
    <text class="node-text" x="303" y="123">Lorem Ipsum</text>
    <text class="node-text" x="303" y="132">is simply text</text>
    <text class="node-text" x="476" y="138">Lorem Ipsum</text>
    <text class="node-text" x="476" y="147">is simply text</text>
    <text class="node-text" x="535" y="190" fill="#333">Lorem Ipsum</text>
    <text class="node-text" x="535" y="199" fill="#333">is simply</text>
    <text class="node-text" x="535" y="208" fill="#333">text</text>
    <text class="node-text" x="261" y="212">Lorem Ipsum</text>
    <text class="node-text" x="261" y="221">is simply text</text>
    <text class="node-text" x="308" y="277">Lorem Ipsum</text>
    <text class="node-text" x="308" y="286">is simply text</text>
    <text class="node-text" x="380" y="316">Lorem Ipsum is</text>
    <text class="node-text" x="380" y="325">simply dummy</text>
    <text class="node-text" x="380" y="334">text</text>
    <text class="node-text" x="490" y="274">Lorem Ipsum is</text>
    <text class="node-text" x="490" y="283">simply dummy text</text>
    <text class="node-text" x="490" y="292">of the printing</text>
  </g>

  <g text-anchor="end">
    <text class="hub-title" x="278" y="46">Sample Text Here</text>
    <text class="hub-body" x="278" y="61">Lorem Ipsum is simply</text>
    <text class="hub-body" x="278" y="74">dummy text of the printing</text>
    <text class="hub-title" x="168" y="194">Sample Text Here</text>
    <text class="hub-body" x="168" y="209">Lorem Ipsum is simply</text>
    <text class="hub-body" x="168" y="222">dummy text of the printing</text>
    <text class="hub-title" x="237" y="295">Sample Text Here</text>
    <text class="hub-body" x="237" y="310">Lorem Ipsum is simply</text>
    <text class="hub-body" x="237" y="323">dummy text of the printing</text>
  </g>
  <g>
    <text class="hub-title" x="376" y="43">Sample Text Here</text>
    <text class="hub-body" x="376" y="58">Lorem Ipsum is simply</text>
    <text class="hub-body" x="376" y="71">dummy text of the printing</text>
    <text class="hub-title" x="555" y="82">Sample Text Here</text>
    <text class="hub-body" x="555" y="97">Lorem Ipsum is simply</text>
    <text class="hub-body" x="555" y="110">dummy text of the printing</text>
    <text class="hub-title" x="614" y="169">Sample Text Here</text>
    <text class="hub-body" x="614" y="184">Lorem Ipsum is simply</text>
    <text class="hub-body" x="614" y="197">dummy text of the printing</text>
    <text class="hub-title" x="606" y="323">Sample Text Here</text>
    <text class="hub-body" x="606" y="338">Lorem Ipsum is simply</text>
    <text class="hub-body" x="606" y="351">dummy text of the printing</text>
  </g>
  <g text-anchor="middle">
    <text class="hub-title" x="312" y="363">Sample Text Here</text>
    <text class="hub-body" x="312" y="378">Lorem Ipsum is simply</text>
    <text class="hub-body" x="312" y="391">dummy text of the printing</text>
  </g>

  <rect x="0" y="405" width="180" height="22" fill="var(--footer-grey)"/>
  <circle cx="20" cy="416" r="5" fill="none" stroke="var(--white)" stroke-width="1.2"/>
  <text class="footer-url" x="34" y="420">www.webaddress.com | 3</text>
  <line x1="194" y1="416" x2="650" y2="416" stroke="#6f9fb5" stroke-width="1"/>
  <circle cx="191" cy="416" r="3" fill="none" stroke="#9fc3d1"/>
  <text class="brand" x="765" y="423" font-size="22" text-anchor="end" fill="#7a5cae">Veltrano</text>
</svg>

<!-- Quadrant ring slide -->
<svg class="slide ring-slide" viewBox="0 0 782 440" xmlns="http://www.w3.org/2000/svg">
  <defs>
    <path id="arc-tl" d="M310 196 A97 97 0 0 1 372 137"/>
    <path id="arc-tr" d="M410 137 A97 97 0 0 1 472 196"/>
    <path id="arc-bl" d="M300 252 A97 97 0 0 0 362 320"/>
    <path id="arc-br" d="M420 320 A97 97 0 0 0 484 252"/>
  </defs>
  <rect width="782" height="440" fill="var(--white)"/>
  <rect width="782" height="60" fill="var(--ink)"/>
  <circle cx="49" cy="30" r="18" fill="none" stroke="var(--sky)" stroke-width="2"/>
  <text class="heading" x="78" y="38" font-size="21">HEADING GOES HERE</text>

  <g fill="var(--azure)">
    <rect x="54" y="185" width="230" height="41"/>
    <rect x="54" y="240" width="230" height="42"/>
    <rect x="500" y="185" width="230" height="41"/>
    <rect x="500" y="240" width="230" height="42"/>
  </g>
  <circle cx="392" cy="232" r="145" fill="var(--lilac)"/>
  <circle cx="392" cy="232" r="123" fill="var(--purple)"/>
  <circle cx="392" cy="232" r="72" fill="var(--white)"/>
  <g fill="var(--white)">
    <rect x="389" y="86" width="6" height="76"/>
    <rect x="389" y="302" width="6" height="76"/>
    <rect x="246" y="229" width="76" height="6"/>
    <rect x="462" y="229" width="76" height="6"/>
  </g>
  <text class="arc-text"><textPath href="#arc-tl" startOffset="50%" text-anchor="middle">Sample Text Here</textPath></text>
  <text class="arc-text"><textPath href="#arc-tr" startOffset="50%" text-anchor="middle">Sample Text Here</textPath></text>
  <text class="arc-text"><textPath href="#arc-bl" startOffset="50%" text-anchor="middle">Sample Text Here</textPath></text>
  <text class="arc-text"><textPath href="#arc-br" startOffset="50%" text-anchor="middle">Sample Text Here</textPath></text>
  <text class="brand" x="392" y="241" font-size="27" text-anchor="middle">Veltrano</text>

  <g text-anchor="middle">
    <text class="band-text" x="156" y="202">Lorem Ipsum is simply dummy text of the</text>
    <text class="band-text" x="156" y="216">printing and typesetting industry.</text>
    <text class="band-text" x="156" y="257">Lorem Ipsum is simply dummy text of the</text>
    <text class="band-text" x="156" y="271">printing and typesetting industry.</text>
  </g>
  <g>
    <text class="band-text" x="527" y="202">Lorem Ipsum is simply dummy text of the</text>
    <text class="band-text" x="527" y="216">printing and typesetting industry.</text>
    <text class="band-text" x="527" y="257">Lorem Ipsum is simply dummy text of the</text>
    <text class="band-text" x="527" y="271">printing and typesetting industry.</text>
  </g>

  <rect x="0" y="405" width="180" height="22" fill="var(--footer-grey)"/>
  <circle cx="20" cy="416" r="5" fill="none" stroke="var(--white)" stroke-width="1.2"/>
  <text class="footer-url" x="34" y="420">www.webaddress.com | 4</text>
  <line x1="194" y1="416" x2="650" y2="416" stroke="#9aa0a6" stroke-width="1"/>
  <circle cx="191" cy="416" r="3" fill="var(--white)" stroke="#9aa0a6"/>
  <text class="brand" x="765" y="423" font-size="22" text-anchor="end">Veltrano</text>
</svg>

<!-- Data slide -->
<svg class="slide data-slide" viewBox="0 0 782 440" xmlns="http://www.w3.org/2000/svg">
  <defs>
    <linearGradient id="data-bg" x1="0" y1="0" x2="0.3" y2="1">
      <stop offset="0" stop-color="#123f74"/>
      <stop offset="0.55" stop-color="#15587e"/>
      <stop offset="1" stop-color="#1a9a8c"/>
    </linearGradient>
  </defs>
  <rect width="782" height="440" fill="url(#data-bg)"/>
  <text x="391" y="57" font-size="27" font-weight="700" fill="var(--sky)" text-anchor="middle">HEADING GOES HERE</text>
  <g font-size="9.6" fill="var(--white)">
    <text x="38" y="89">Lorem Ipsum is simply dummy text of the printing and typesetting industry. Lorem Ipsum has been the industry's standard dummy text ever since the 1500s,</text>
    <text x="38" y="103">when an unknown printer took a galley of type and scrambled it to make a type specimen book. It has survived not only five centuries, but also the leap into</text>
    <text x="38" y="117">electronic typesetting, remaining essentially unchanged.</text>
  </g>

  <text class="group-label" x="38" y="163">TEXT GOES HERE</text>
  <text class="group-label" x="38" y="286">TEXT GOES HERE</text>

  <g color="#ffffff">
    <use href="#icon-person" x="70" y="178" width="12" height="30"/>
    <use href="#icon-person" x="88" y="178" width="12" height="30"/>
    <use href="#icon-person" x="106" y="178" width="12" height="30"/>
    <use href="#icon-person" x="124" y="178" width="12" height="30"/>
    <use href="#icon-person" x="70" y="221" width="12" height="30"/>
    <use href="#icon-person" x="88" y="221" width="12" height="30"/>
    <use href="#icon-person" x="106" y="221" width="12" height="30"/>
    <use href="#icon-person" x="124" y="221" width="12" height="30"/>
    <use href="#icon-person" x="142" y="221" width="12" height="30"/>
    <use href="#icon-person" x="160" y="221" width="12" height="30"/>
    <use href="#icon-person" x="70" y="301" width="12" height="30"/>
    <use href="#icon-person" x="88" y="301" width="12" height="30"/>
    <use href="#icon-person" x="106" y="301" width="12" height="30"/>
    <use href="#icon-person" x="124" y="301" width="12" height="30"/>
    <use href="#icon-person" x="142" y="301" width="12" height="30"/>
    <use href="#icon-person" x="70" y="344" width="12" height="30"/>
    <use href="#icon-person" x="88" y="344" width="12" height="30"/>
    <use href="#icon-person" x="106" y="344" width="12" height="30"/>
    <use href="#icon-person" x="124" y="344" width="12" height="30"/>
    <use href="#icon-person" x="142" y="344" width="12" height="30"/>
    <use href="#icon-person" x="160" y="344" width="12" height="30"/>
    <use href="#icon-person" x="178" y="344" width="12" height="30"/>
  </g>
  <g color="#0b1f3a">
    <use href="#icon-person" x="142" y="178" width="12" height="30"/>
    <use href="#icon-person" x="160" y="178" width="12" height="30"/>
    <use href="#icon-person" x="178" y="178" width="12" height="30"/>
    <use href="#icon-person" x="196" y="178" width="12" height="30"/>
    <use href="#icon-person" x="214" y="178" width="12" height="30"/>
    <use href="#icon-person" x="232" y="178" width="12" height="30"/>
    <use href="#icon-person" x="178" y="221" width="12" height="30"/>
    <use href="#icon-person" x="196" y="221" width="12" height="30"/>
    <use href="#icon-person" x="214" y="221" width="12" height="30"/>
    <use href="#icon-person" x="232" y="221" width="12" height="30"/>
    <use href="#icon-person" x="160" y="301" width="12" height="30"/>
    <use href="#icon-person" x="178" y="301" width="12" height="30"/>
    <use href="#icon-person" x="196" y="301" width="12" height="30"/>
    <use href="#icon-person" x="214" y="301" width="12" height="30"/>
    <use href="#icon-person" x="232" y="301" width="12" height="30"/>
    <use href="#icon-person" x="196" y="344" width="12" height="30"/>
    <use href="#icon-person" x="214" y="344" width="12" height="30"/>
    <use href="#icon-person" x="232" y="344" width="12" height="30"/>
  </g>
  <text class="pct" x="257" y="195">40%</text>
  <text class="pct" x="257" y="238">60%</text>
  <text class="pct" x="257" y="318">50%</text>
  <text class="pct" x="257" y="361">70%</text>

  <g stroke="#d6e6ee" stroke-width="0.8">
    <line x1="440" y1="156" x2="740" y2="156"/>
    <line x1="440" y1="200" x2="740" y2="200"/>
    <line x1="440" y1="245" x2="740" y2="245"/>
    <line x1="440" y1="289" x2="740" y2="289"/>
    <line x1="440" y1="333" x2="740" y2="333"/>
    <line x1="440" y1="377" x2="740" y2="377"/>
  </g>
  <g text-anchor="end">
    <text class="chart-label" x="427" y="159">100</text>
    <text class="chart-label" x="427" y="203">80</text>
    <text class="chart-label" x="427" y="248">60</text>
    <text class="chart-label" x="427" y="292">40</text>
    <text class="chart-label" x="427" y="336">20</text>
    <text class="chart-label" x="427" y="380">0</text>
  </g>
  <g fill="var(--line-blue)">
    <rect x="466" y="266" width="13" height="111"/>
    <rect x="500" y="200" width="13" height="177"/>
    <rect x="532" y="244" width="13" height="133"/>
    <rect x="567" y="324" width="13" height="53"/>
    <rect x="600" y="156" width="13" height="221"/>
    <rect x="636" y="200" width="13" height="177"/>
    <rect x="668" y="236" width="13" height="141"/>
    <rect x="702" y="302" width="13" height="75"/>
  </g>
  <g text-anchor="middle">
    <text class="chart-label" x="472" y="262">50%</text>
    <text class="chart-label" x="506" y="196">80%</text>
    <text class="chart-label" x="538" y="240">60%</text>
    <text class="chart-label" x="573" y="320">24%</text>
    <text class="chart-label" x="606" y="152">100%</text>
    <text class="chart-label" x="642" y="196">80%</text>
    <text class="chart-label" x="674" y="232">64%</text>
    <text class="chart-label" x="708" y="298">34%</text>
  </g>

  <rect x="0" y="405" width="180" height="22" fill="var(--footer-grey)"/>
  <circle cx="20" cy="416" r="5" fill="none" stroke="var(--white)" stroke-width="1.2"/>
  <text class="footer-url" x="34" y="420">www.webaddress.com | 5</text>
  <line x1="194" y1="416" x2="650" y2="416" stroke="#6f9fb5" stroke-width="1"/>
  <circle cx="191" cy="416" r="3" fill="none" stroke="#9fc3d1"/>
  <text class="brand" x="765" y="423" font-size="22" text-anchor="end" fill="#7a5cae">Veltrano</text>
</svg>

</body>
</html>
```